Business Card design for insurance broker in Denver, CO, USA

I need a business card designed using this logo that was just created. We sell life and disability income insurance to US consumers.
Looking for a professionally designed card to make use of the logo and have something to hand to prospects or new business referral sources. The card could be white, gray, black or whatever you would recommend.

Target Market(s)

US Consumers and other financial professionals that I partner with.

Industry/Entity Type

Insurance Broker

Contact Information for Business Card

Owen T. Farrow, CLU, LUTCF (please note that CLU should have a superscript R in a circle for registered trademark)
President
phone (303) 555-0187
email owen@keelbrookcover.example
4620 W. Halvern Rd, Suite 300, Greenwood Village, CO 80111
Somewhere fit in a tagline saying "Your resource for life, long term care, and disability insurance" (maybe the back if it doesn't fit on the front, your call)

Font styles to use
Sans Serif

Requirements
Must have
• Must have logo in correct blue and gray colors, my name, address, phone, email. Order and placement determined by the designer.
• I just want something that looks a more professional than what I could have done using the business card designer tool on pixelbazaar.example or QuillPress, or any other do-it-yourself tool
• A regular rectangular business card with square corners is preferred
Nice to have
• I included the logos of 2 organizations I belong to (GKLS and WOBCE). They should be small, but visible on the back only. If it doesn’t look good, this is not a requirement, feel free to drop it.
Should not have
• Do not add any colors not already in the logo, except use of black and whites which are okay. If you use the logo on the back and want to make that in all black, gray or white, that may be okay as well.

```html
<!DOCTYPE html>
<html lang="en">
<head>
<meta charset="utf-8">
<title>Keelbrook Cover – Business Card</title>
<link rel="stylesheet" href="https://fonts.googleapis.com/css2?family=Montserrat:wght@400;500;600;700&display=swap">
<style>
  :root{
    --bg:#ececec;
    --paper:#ffffff;
    --blue:#1e86c8;
    --gray:#8c8c8c;
    --badge:#6db0df;
  }
  *{margin:0;padding:0;box-sizing:border-box}
  html,body{width:1200px;height:1200px;overflow:hidden;background:var(--bg);font-family:"Montserrat",sans-serif}
  .card{position:absolute;left:235px;width:701px;height:377px}
  .card-front{top:168px;background:var(--paper)}
  .card-back{top:635px;background:var(--blue)}

  .holder{position:absolute;left:21px;top:34px}
  .holder-name{font-size:20px;font-weight:700;color:var(--blue);white-space:nowrap}
  .holder-name .credentials{color:var(--gray);font-weight:600}
  .holder-name sup{font-size:10px;font-weight:500}
  .holder-title{margin-top:6px;font-size:20px;font-weight:700;letter-spacing:5px;color:var(--blue)}

  .brand{position:absolute;display:flex;align-items:center}
  .brand-front{right:26px;top:24px;gap:14px}
  .brand-mark{border-radius:50%;border:4px solid var(--blue)}
  .brand-front .brand-mark{width:80px;height:80px}
  .brand-name{font-weight:700;line-height:1.02;color:var(--blue)}
  .brand-front .brand-name{font-size:28px}
  .brand-back{left:41px;top:120px;gap:22px}
  .brand-back .brand-mark{width:115px;height:115px;border-color:#fff}
  .brand-back .brand-name{font-size:40px;color:#fff}

  .rule{position:absolute;left:22px;right:22px;height:3px;background:var(--blue)}
  .rule-top{top:144px}
  .rule-bottom{top:246px}

  .contact{position:absolute;display:flex;align-items:center;gap:10px;font-size:12.5px;color:var(--gray);line-height:1.3}
  .contact svg{flex:none;fill:var(--blue)}
  .contact-address{left:30px;top:166px}
  .contact-phone{left:30px;top:217px}
  .contact-email{left:448px;top:170px;font-size:11.5px}
  .contact-web{left:448px;top:214px;font-size:11.5px}

  .tagline{position:absolute;left:0;right:0;top:290px;text-align:center;font-size:17px;font-weight:700;letter-spacing:1.2px;line-height:1.3;color:var(--blue)}

  .badge{position:absolute;background:var(--badge)}
  .badge-triangle{left:485px;top:41px;width:150px;height:80px;clip-path:polygon(50% 0,100% 100%,0 100%)}
  .badge-round{left:497px;top:210px;width:118px;height:90px;border-radius:50%}
</style>
</head>
<body>
  <section class="card card-front">
    <div class="holder">
      <p class="holder-name">Owen T. Farrow, <span class="credentials">CLU<sup>®</sup>, LUTCF</span></p>
      <p class="holder-title">PRESIDENT</p>
    </div>

    <div class="brand brand-front">
      <span class="brand-mark"></span>
      <p class="brand-name">KEELBROOK<br>COVER</p>
    </div>

    <div class="rule rule-top"></div>

    <p class="contact contact-address">
      <svg width="18" height="24" viewBox="0 0 18 24" aria-hidden="true"><path d="M9 0a9 9 0 0 0-9 9c0 6.5 9 15 9 15s9-8.5 9-15a9 9 0 0 0-9-9zm0 12.5A3.5 3.5 0 1 1 9 5.5a3.5 3.5 0 0 1 0 7z"/></svg>
      <span>4620 W. Halvern Rd, Suite 300,<br>Larkmont Village, CO 80940</span>
    </p>
    <p class="contact contact-phone">
      <svg width="20" height="20" viewBox="0 0 24 24" aria-hidden="true"><path d="M6.6 10.8a15.1 15.1 0 0 0 6.6 6.6l2.2-2.2a1 1 0 0 1 1-.25 11.4 11.4 0 0 0 3.6.57 1 1 0 0 1 1 1V20a1 1 0 0 1-1 1A17 17 0 0 1 3 4a1 1 0 0 1 1-1h3.5a1 1 0 0 1 1 1c0 1.25.2 2.45.57 3.57a1 1 0 0 1-.25 1z"/></svg>
      <span>(303) 555-0187</span>
    </p>
    <p class="contact contact-email">
      <svg width="22" height="16" viewBox="0 0 22 16" aria-hidden="true"><path d="M0 0h22v16H0z"/><path d="M1 1l10 8 10-8M1 15l7-6M21 15l-7-6" stroke="#fff" stroke-width="1.3" fill="none"/></svg>
      <span>owen@keelbrookcover.example</span>
    </p>
    <p class="contact contact-web">
      <svg width="20" height="20" viewBox="0 0 20 20" aria-hidden="true"><circle cx="10" cy="10" r="10"/><path d="M0 10h20M10 0v20M3 4.5h14M3 15.5h14M10 0c-4 3-4 17 0 20M10 0c4 3 4 17 0 20" stroke="#fff" stroke-width="1.1" fill="none"/></svg>
      <span>www.keelbrookcover.example</span>
    </p>

    <div class="rule rule-bottom"></div>

    <p class="tagline">YOUR RESOURCE FOR LIFE, LONG TERM CARE,<br>AND DISABILITY INSURANCE</p>
  </section>

  <section class="card card-back">
    <div class="brand brand-back">
      <span class="brand-mark"></span>
      <p class="brand-name">KEELBROOK<br>COVER</p>
    </div>
    <div class="badge badge-triangle" role="img" aria-label="WOBCE membership badge"></div>
    <div class="badge badge-round" role="img" aria-label="GKLS membership badge"></div>
  </section>
</body>
</html>
```